Heron Loan Partners Business Card

We need a business card design for our mortgage servicing company. In addition to servicing the loans of homeowners, we help homeowners with purchasing their homes and any mortgage refinancing. We would like to see designs that use the colors in the logo attached below (gold-ish yellow and navy blue), and any other design you deem fit! The design should communicate a simpler life with smart mortgages provided by Heron.

```html
<!DOCTYPE html>
<html lang="en">
<head>
<meta charset="utf-8">
<title>Heron Loan Partners Business Card</title>
<link rel="stylesheet" href="https://fonts.googleapis.com/css2?family=Playfair+Display:wght@700&family=Poppins:wght@400&display=swap">
<style>
  :root {
    --gold: #e0b140;
    --navy: #23204f;
    --paper: #ffffff;
    --backdrop: #2a2523;
  }
  * { margin: 0; padding: 0; box-sizing: border-box; }
  html, body {
    width: 1200px;
    height: 842px;
    overflow: hidden;
    background: var(--backdrop);
  }
  .canvas {
    position: relative;
    width: 1200px;
    height: 842px;
  }
  .card {
    position: absolute;
    top: 266px;
    width: 540px;
    height: 309px;
    background: var(--paper);
    overflow: hidden;
  }
  .card--back { left: 40px; }
  .card--front { left: 620px; }

  /* Back: contact side */
  .band {
    position: absolute;
    left: 0;
    width: 100%;
    height: 16px;
    background: var(--gold);
  }
  .band--top { top: 0; }
  .band--bottom { bottom: 0; }
  .contact {
    position: absolute;
    inset: 16px 0;
    display: flex;
    flex-direction: column;
    align-items: center;
    justify-content: center;
    text-align: center;
    color: var(--navy);
    font-family: 'Poppins', sans-serif;
    text-transform: uppercase;
    font-size: 13px;
    line-height: 1.3;
    letter-spacing: 0.3px;
  }
  .contact__name {
    font-family: 'Playfair Display', serif;
    font-weight: 700;
    font-size: 22px;
    text-transform: none;
    letter-spacing: 0;
    line-height: 1.1;
  }
  .contact__role { font-size: 12px; }
  .rule {
    width: 70px;
    height: 1.5px;
    background: var(--gold);
    margin: 10px 0 12px;
  }
  .contact__phone { font-size: 15px; }

  /* Front: brand side */
  .accent {
    position: absolute;
    background: var(--gold);
  }
  .accent--left { left: 0; top: 152px; width: 48px; height: 62px; }
  .accent--right { right: 0; top: 54px; width: 48px; height: 42px; }
  .stroke {
    position: absolute;
    width: 5px;
    background: var(--navy);
  }
  .stroke--left { left: 54px; top: 146px; height: 74px; }
  .stroke--right { right: 54px; top: 48px; height: 54px; }
  .brand {
    position: absolute;
    inset: 0;
    display: flex;
    align-items: center;
    justify-content: center;
    gap: 12px;
  }
  .brand__mark {
    width: 18px;
    height: 18px;
    background: var(--gold);
  }
  .brand__name {
    font-family: 'Playfair Display', serif;
    font-weight: 700;
    font-size: 34px;
    color: var(--navy);
  }
</style>
</head>
<body>
<main class="canvas">
  <section class="card card--back" aria-label="Contact side">
    <div class="band band--top"></div>
    <div class="contact">
      <p class="contact__name">Daniel Hartley</p>
      <p class="contact__role">Managing Director</p>
      <span class="rule"></span>
      <p class="contact__phone">044-987 654 321</p>
      <p>info@heronloans.com</p>
      <p>www.heronloans.com</p>
      <span class="rule"></span>
      <p>18, Willow Bank Road</p>
      <p>30417, Eastbrook</p>
    </div>
    <div class="band band--bottom"></div>
  </section>

  <section class="card card--front" aria-label="Brand side">
    <div class="accent accent--left"></div>
    <div class="stroke stroke--left"></div>
    <div class="accent accent--right"></div>
    <div class="stroke stroke--right"></div>
    <div class="brand">
      <span class="brand__mark"></span>
      <span class="brand__name">Heron Loan Partners</span>
    </div>
  </section>
</main>
</body>
</html>
```